Preisliste für Kosmetikinstitut
Zielgruppe
Ich benötige für mein Kosmetikinstitut eine Preisliste für die moderne Frau, aber auch Männer. Das Design sollte mein Logo enthalten. Farben des Designkonzepts einbauen.
A4 quer zum Falten, wie ein Heft, 1. Seite Preisliste mit logo, im Innenteil dann Anwendungen
Aufgabenstellung
Minimalistisch, ästhetisch, modern, edel
Kontaktdaten auf der Rückseite
LB Hautatelier
Lotte Brenner
Lindenhang 17
83671 Waakirchen
EMail: lotte@lb-hautatelier.de
Whatsapp: 0176 284 9017

```html
<!DOCTYPE html>
<html lang="de">
<head>
<meta charset="utf-8">
<title>LB Hautatelier – Preisliste Titelseiten</title>
<link rel="stylesheet" href="https://fonts.googleapis.com/css2?family=Questrial&family=Arimo:ital,wght@1,700&display=swap">
<style>
  :root {
    --canvas: #ffffff;
    --paper: #fbfbf4;
    --ink: #6d7876;
    --shadow: rgba(0, 0, 0, 0.08);
    --pattern-light: #eef0ec;
    --pattern-dark: #c9cfcb;
  }
  html, body {
    margin: 0;
    padding: 0;
    width: 1200px;
    height: 1200px;
    overflow: hidden;
    background: var(--canvas);
  }
  .cover {
    position: absolute;
    top: 224px;
    height: 758px;
    background: var(--paper);
    box-shadow: 0 2px 10px var(--shadow);
  }
  .cover--plain { left: 68px; width: 512px; }
  .cover--pattern { left: 591px; width: 549px; }

  .brand {
    position: absolute;
    top: 190px;
    display: flex;
    align-items: center;
    gap: 14px;
    transform: translateX(-50%);
    white-space: nowrap;
  }
  .cover--plain .brand { left: 265px; }
  .cover--pattern .brand { left: 278px; }

  .brand-name {
    margin: 0;
    font-family: "Questrial", sans-serif;
    font-weight: 400;
    font-size: 40px;
    line-height: 1;
    letter-spacing: 0.5px;
    color: var(--ink);
  }
  .brand-mark {
    flex: none;
    width: 16px;
    height: 16px;
    border-radius: 50%;
    background: var(--ink);
  }

  .title-rule {
    position: absolute;
    top: 537px;
    width: 1px;
    height: 172px;
    background: var(--ink);
  }
  .cover--plain .title-rule { left: 66px; }
  .cover--pattern .title-rule { left: 93px; }

  .cover-title {
    position: absolute;
    top: 568px;
    margin: 0;
    font-family: "Arimo", sans-serif;
    font-style: italic;
    font-weight: 700;
    font-size: 27px;
    color: var(--ink);
    writing-mode: vertical-rl;
    transform: rotate(180deg);
    line-height: 1;
  }
  .cover--plain .cover-title { left: 76px; }
  .cover--pattern .cover-title { left: 103px; }

  .ornament-strip {
    position: absolute;
    left: 35px;
    top: 546px;
    width: 45px;
    height: 157px;
    background: linear-gradient(160deg, var(--pattern-light), var(--pattern-dark) 45%, var(--pattern-light) 70%, var(--pattern-dark));
  }
</style>
</head>
<body>
  <section class="cover cover--plain">
    <div class="brand">
      <h1 class="brand-name">LB Hautatelier</h1>
      <span class="brand-mark"></span>
    </div>
    <span class="title-rule"></span>
    <h2 class="cover-title">Preisliste</h2>
  </section>

  <section class="cover cover--pattern">
    <div class="brand">
      <h1 class="brand-name">LB Hautatelier</h1>
      <span class="brand-mark"></span>
    </div>
    <div class="ornament-strip" role="img" aria-label="Schmaler Streifen mit feinem, geschwungenem Linienornament in Grautönen"></div>
    <span class="title-rule"></span>
    <h2 class="cover-title">Preisliste</h2>
  </section>
</body>
</html>
```